Modernize Website: marcusfellwright.net

I am a novelist with an older-generation website at: marcusfellwright.net.

I am hoping to refresh this outdated website with a new, responsive redesign. I would prefer to host the code myself, and edit using Adobe Dreamweaver. So I’m not looking to use a hosted site builder like Plexo. Nor am I looking to use a CMS like Pagecraft.

In order to simplify the old site, there are a number of sections I’ll be looking to remove during this redesign. These are shown in the "MF Site Redesign" attachment. I can also provide imagery for new content (another book series in addition to the existing one), as well as higher-resolution imagery (if needed) of the old content.

Happy to answer any further questions.
Updates

I've uploaded a ZIP file containing high-res artwork associated with the new trilogy of books.

Target Market(s)

Readers of epic fantasy novels such as H.W.B. Castellane's THE WARDEN OF THE VALES, Harold P.Q. Ventris's A CROWN OF ASH AND RAIN, Victor Halloway's THE GATE OF STARS, or Dennis Vale's BLADE OF MERIVANE.

Industry/Entity Type

Entertainment

Coding

Coded - Design and coding required

Number of Pages Required

5+ page

Font styles to use
Serif
Decorative

Colors

Designer to choose colors to be used in the design.

Requirements
Must have
• I'm looking for a responsive design that displays nicely on both mobile and desktop devices. Existing site contains multiple pages, but these can obviously be combined into fewer pages (or even one) by divisions such as tabs, sections, and/or modal windows. See marcusfellwright.net for current content and "MF Site Redesign" attachment for content to be removed at this time.
Nice to have
• The ability to fulfill orders of autographed books directly from the website. I currently use Coinlo to do this, but it would be nice to incorporate a more comprehensive merchant service at a reasonable rate.
Should not have
• I'd like to host and control the site code myself. So please don't use a hosted web builder like Plexo, or a cloud-based CMS like Pagecraft.

```html
<!DOCTYPE html>
<html lang="en">
<head>
<meta charset="utf-8">
<title>Marcus Fellwright – The Legend of Varnholt</title>
<link href="https://fonts.googleapis.com/css2?family=Oswald:wght@400;500;600&family=Open+Sans:wght@400;600;700&display=swap" rel="stylesheet">
<style>
  :root{
    --red:#e3000f;
    --red-deep:#8d0410;
    --black:#000;
    --ink:#0b0b0b;
    --footer:#141414;
    --white:#fff;
    --muted:#e6e6e6;
    --head:"Oswald", sans-serif;
    --body:"Open Sans", sans-serif;
  }
  *{margin:0;padding:0;box-sizing:border-box}
  html,body{width:1200px;height:2560px;overflow:hidden;background:var(--black)}
  body{position:relative;font-family:var(--body);color:var(--white)}

  /* header */
  .site-header{position:absolute;top:0;left:0;width:1200px;height:106px;background:#131313;z-index:3}
  .brand{position:absolute;left:94px;top:34px;display:flex;align-items:center;gap:12px;font-family:var(--head);font-weight:500;font-size:26px;letter-spacing:1px;color:var(--white);text-transform:uppercase}
  .brand-mark{width:14px;height:14px;background:var(--red)}
  .main-nav a{position:absolute;top:40px;font-family:var(--head);font-weight:500;font-size:18px;color:var(--white);text-decoration:none;letter-spacing:.3px}
  .main-nav a.active{color:var(--red)}
  .nav-search{position:absolute;left:1086px;top:44px}

  /* hero */
  .hero{position:absolute;top:106px;left:0;width:1200px;height:517px;overflow:hidden}
  .hero-art{position:absolute;inset:0;background:
    radial-gradient(ellipse 260px 160px at 600px 280px,rgba(190,40,20,.75),transparent 70%),
    radial-gradient(ellipse 500px 300px at 420px 200px,#4a3c3a,transparent 75%),
    linear-gradient(180deg,#3b3939 0%,#2b2727 55%,#3a2521 100%)}
  .hero-title{position:absolute;top:150px;width:100%;text-align:center;font-family:var(--head);font-weight:500;font-size:76px;letter-spacing:.5px}
  .slider-dots{position:absolute;top:454px;left:539px;display:flex;gap:4px}
  .slider-dots span{width:28px;height:4px;background:var(--white)}
  .slider-dots span.current{background:var(--red)}

  /* novels */
  .novels{position:absolute;top:623px;left:0;width:1200px;height:580px;background:
    radial-gradient(ellipse 420px 330px at 860px 300px,#2a2522,transparent 75%),var(--black)}
  .section-title{font-family:var(--head);font-weight:500;font-size:64px;line-height:1}
  .novels .section-title{position:absolute;left:99px;top:112px}
  .novels-text{position:absolute;left:101px;top:206px;width:530px;font-size:14.4px;line-height:26px;color:var(--muted)}
  .btn{position:absolute;display:flex;align-items:center;justify-content:center;background:var(--red);color:var(--white);font-weight:700;font-size:15px;text-transform:uppercase;text-decoration:none}
  .novels .btn{left:101px;top:399px;width:133px;height:51px}
  .book-cover{position:absolute;left:722px;top:77px;width:302px;height:427px;background:linear-gradient(180deg,#2f3d3c 0%,#3a3024 45%,#b5461b 75%,#4a1d10 100%);box-shadow:14px 10px 0 -2px #d8d8d8,18px 14px 30px rgba(0,0,0,.7)}

  /* world */
  .world{position:absolute;top:1203px;left:0;width:1200px;height:598px;background:
    radial-gradient(ellipse 500px 300px at 820px 160px,#c20c18,transparent 75%),
    linear-gradient(160deg,#b10612 0%,#7c030c 50%,#c80814 100%)}
  .world .section-title{position:absolute;width:100%;top:78px;text-align:center}
  .world-text{position:absolute;left:220px;top:170px;width:760px;text-align:center;font-size:14.4px;line-height:29px;color:var(--white)}
  .world-cards{position:absolute;left:99px;top:299px;display:flex;gap:17px}
  .world-card{width:237px;height:224px;border:2px solid var(--white);background:var(--white);display:flex;flex-direction:column}
  .world-card .card-art{height:172px}
  .world-card .card-label{flex:1;display:flex;align-items:center;justify-content:center;color:#1c1c1c;font-weight:600;font-size:21px;text-transform:uppercase}
  .art-maps{background:linear-gradient(135deg,#1b3354,#6b5a3e 55%,#203e62)}
  .art-characters{background:linear-gradient(180deg,#8a8074,#5c4a3c 60%,#6a7070)}
  .art-locations{background:linear-gradient(180deg,#2e3240,#59523c 55%,#3a4a36)}
  .art-artifacts{background:linear-gradient(150deg,#2a2420,#6e5a4a 55%,#1c1816)}

  /* author */
  .author{position:absolute;top:1801px;left:0;width:1200px;height:575px;background:
    radial-gradient(ellipse 320px 300px at 200px 240px,#2a2524,transparent 75%),var(--ink)}
  .author-photo{position:absolute;left:99px;top:82px;width:382px;height:382px;border-radius:50%;border:5px solid var(--white);background:linear-gradient(180deg,#c9d6de 0%,#9fb0b8 50%,#cdbfa8 100%)}
  .author .section-title{position:absolute;left:563px;top:100px}
  .author-text{position:absolute;left:563px;top:190px;width:560px;font-size:14.2px;line-height:26.5px;color:var(--muted)}
  .author .btn{left:563px;top:386px;width:135px;height:51px}

  /* footer */
  .site-footer{position:absolute;top:2376px;left:0;width:1200px;height:184px;background:var(--footer);overflow:hidden}
  .footer-accent{position:absolute;top:0;left:0}
  .contact-line{position:absolute;left:104px;display:flex;align-items:center;gap:8px;font-size:14px;color:var(--white)}
  .contact-line .sep{margin:0 8px}
  .footer-links{position:absolute;left:102px;top:123px;font-size:14px;color:var(--white)}
  .footer-links a{color:var(--white);text-decoration:none}
  .footer-links .sep{margin:0 7px}
  .social{position:absolute;top:42px;left:876px;display:flex;gap:8px}
  .social a{width:50px;height:50px;border:2px solid var(--white);border-radius:50%;display:flex;align-items:center;justify-content:center}
  .copyright{position:absolute;left:722px;top:117px;font-size:14px;color:var(--white)}
</style>
</head>
<body>

<header class="site-header">
  <div class="brand"><span class="brand-mark"></span>Marcus Fellwright</div>
  <nav class="main-nav">
    <a href="#" class="active" style="left:589px">HOME</a>
    <a href="#" style="left:678px">NOVELS</a>
    <a href="#" style="left:777px">WORLD</a>
    <a href="#" style="left:872px">AUTHOR</a>
    <a href="#" style="left:976px">CONTACT</a>
  </nav>
  <svg class="nav-search" width="18" height="18" viewBox="0 0 18 18" aria-label="Search"><circle cx="7.5" cy="7.5" r="5.5" fill="none" stroke="#fff" stroke-width="2.4"/><line x1="11.5" y1="11.5" x2="16" y2="16" stroke="#fff" stroke-width="2.8" stroke-linecap="round"/></svg>
</header>

<section class="hero">
  <div class="hero-art" role="img" aria-label="Painting of a great dragon breathing fire at a lone warrior on a rocky ridge"></div>
  <h1 class="hero-title">THE LEGEND OF VARNHOLT</h1>
  <div class="slider-dots"><span class="current"></span><span></span><span></span><span></span></div>
</section>

<section class="novels">
  <h2 class="section-title">NOVELS</h2>
  <p class="novels-text">Sed ut perspiciatis unde omnis iste natus error sit voluptatem accusantium doloremque laudantium, totam rem aperiam, eaque ipsa quae ab illo inven tore veritatis et quasi architecto beatae vitae dicta sunt explicabo. Nemo en im ipsam voluptatem quia voluptas sit aspernatur aut odit aut fugit, sed qu ia consequuntur magni dolores eos qui ratione voluptatem sequi nesciunte porro quisquam est, qui dolorem ipsum.</p>
  <a href="#" class="btn">Read More</a>
  <div class="book-cover" role="img" aria-label="Hardcover book The Ember Crown by Marcus Fellwright, fiery dragon artwork on the cover"></div>
</section>

<section class="world">
  <h2 class="section-title">WORLD</h2>
  <p class="world-text">Lorem ipsum dolor sit amet, consectetur adipiscing elit, sed do eiusmod tempor incididunt ut labore et dolore magna aliqua. Ut enim ad minim veniam, quis nostrud exercitation ullamco laboris nisi ut aliquip ex ea commodo consequat. Duis aute irure dolor in reprehenderit in voluptate velit esse cillum</p>
  <div class="world-cards">
    <div class="world-card"><div class="card-art art-maps" role="img" aria-label="Map of the realm"></div><div class="card-label">Maps</div></div>
    <div class="world-card"><div class="card-art art-characters" role="img" aria-label="Illustration of a warrior on a castle wall"></div><div class="card-label">Characters</div></div>
    <div class="world-card"><div class="card-art art-locations" role="img" aria-label="Illustration of a fortress above a waterfall"></div><div class="card-label">Locations</div></div>
    <div class="world-card"><div class="card-art art-artifacts" role="img" aria-label="Illustration of a battle with a dark creature"></div><div class="card-label">Artifacts</div></div>
  </div>
</section>

<section class="author">
  <div class="author-photo" role="img" aria-label="Portrait of the author seated on a beach"></div>
  <h2 class="section-title">AUTHOR</h2>
  <p class="author-text">Weaned on the likes of The Warden of the Vales and Star Reaches, Marcus took to writing fantasy adventure, it seems, almost as soon as he learned to read. By the time he hit grade school, he was writing 30-page stories in lieu of the two or three pages expected of all students on a monthly basis. When at age nine he read Dennis Vale's The Runestones of Merivane, his goal of becoming a fantasy novelist went from child's ambition to hopeless obsession.</p>
  <a href="#" class="btn">Read More</a>
</section>

<footer class="site-footer">
  <svg class="footer-accent" width="1200" height="184" viewBox="0 0 1200 184"><polygon points="742,0 1200,0 1200,184 657,184" fill="var(--red)"/></svg>
  <div class="contact-line" style="top:46px">
    <svg width="10" height="14" viewBox="0 0 10 14"><path d="M5 0a5 5 0 0 0-5 5c0 3.6 5 9 5 9s5-5.4 5-9a5 5 0 0 0-5-5zm0 7a2 2 0 1 1 0-4 2 2 0 0 1 0 4z" fill="#fff"/></svg>
    <span>412 Birchmere Road, Suite 210, Harlow, TX 75301</span><span class="sep">|</span>
    <svg width="13" height="13" viewBox="0 0 24 24"><path d="M6.6 10.8a15.1 15.1 0 0 0 6.6 6.6l2.2-2.2a1 1 0 0 1 1-.25 11.4 11.4 0 0 0 3.6.57 1 1 0 0 1 1 1V20a1 1 0 0 1-1 1A17 17 0 0 1 3 4a1 1 0 0 1 1-1h3.5a1 1 0 0 1 1 1c0 1.25.2 2.45.57 3.57a1 1 0 0 1-.25 1z" fill="#fff"/></svg>
    <span>1 555 010 2040</span>
  </div>
  <div class="contact-line" style="top:81px">
    <svg width="16" height="12" viewBox="0 0 16 12"><rect width="16" height="12" rx="1.5" fill="#fff"/><path d="M1 1.5l7 5 7-5" fill="none" stroke="#141414" stroke-width="1.4"/></svg>
    <span style="margin-left:4px">info@marcusfellwright.net</span>
  </div>
  <nav class="footer-links">
    <a href="#">Help</a><span class="sep">|</span><a href="#">FAQ</a><span class="sep">|</span><a href="#">Support</a><span class="sep">|</span><a href="#">Sitemap</a><span class="sep">|</span><a href="#">Terms Of Use</a><span class="sep">|</span><a href="#">Privacy Statement</a>
  </nav>
  <div class="social">
    <a href="#" aria-label="Share"><svg width="18" height="18" viewBox="0 0 18 18"><circle cx="13.5" cy="3.5" r="2.5" fill="#fff"/><circle cx="4" cy="9" r="2.5" fill="#fff"/><circle cx="13.5" cy="14.5" r="2.5" fill="#fff"/><path d="M13.5 3.5L4 9l9.5 5.5" fill="none" stroke="#fff" stroke-width="1.6"/></svg></a>
    <a href="#" aria-label="Link"><svg width="18" height="18" viewBox="0 0 18 18"><path d="M7.5 10.5l3-3M8 5l1.5-1.5a3 3 0 0 1 4.2 4.2L12.2 9.2M10 13l-1.5 1.5a3 3 0 0 1-4.2-4.2L5.8 8.8" fill="none" stroke="#fff" stroke-width="2" stroke-linecap="round"/></svg></a>
    <a href="#" aria-label="Message"><svg width="18" height="18" viewBox="0 0 18 18"><path d="M2 3h14v9H7l-4 3.5V12H2z" fill="#fff"/></svg></a>
    <a href="#" aria-label="Email"><svg width="20" height="15" viewBox="0 0 16 12"><rect width="16" height="12" rx="1.5" fill="#fff"/><path d="M1 1.5l7 5 7-5" fill="none" stroke="#e3000f" stroke-width="1.4"/></svg></a>
  </div>
  <p class="copyright">Copyrights © 2018, Marcus Fellwright. All rights reserved.</p>
</footer>

</body>
</html>
```